Photographer's price list

I am a photographer who runs a studio (Marrowfield Studio) and need to have a document to send clients detailing my packages (collections) and prices. I have written the text in a word document and need a designer to lay it out for me using my logo and two specific fonts: DejaVu Sans and LainieDaySH.

The look should be clean and modern and keep in the same style as my logo. I will primarily be using the final product as a PDF file to email to potential clients. It should stay black and white.

I would also like to be able to update the text myself as my prices and packages change. So I would like a PSD file.

I think I would like for the document to be in landscape format with "Collections" on one side and A la Carte on the other, but I am open to other ideas.

As for sizing, it should be a standard size so that clients can print it out if they like.

Industry/Entity Type

Landscape

Requirements
Must have
• my logo
fonts: DejaVu and LainieDaySH
Easy to email
Easy to display on one page upon opening
Standard size so that printing from a home computer is easy to do.

```html
<!DOCTYPE html>
<html lang="en">
<head>
<meta charset="utf-8">
<title>Marrowfield Studio – 2013 Photography Collections</title>
<link rel="stylesheet" href="https://fonts.googleapis.com/css2?family=Jost:wght@300;400&family=Oswald:wght@600&family=Open+Sans:wght@400&family=Pathway+Gothic+One&display=swap">
<style>
  :root {
    --backdrop: #e9e7e4;
    --paper: #ffffff;
    --ink: #1b1b1b;
    --ink-soft: #555555;
    --ink-muted: #777777;
    --rule: #c4c4c4;
    --photo-dark: #4a4a4a;
    --photo-mid: #8e8e8e;
    --photo-light: #cfcfcf;
  }
  * { margin: 0; padding: 0; box-sizing: border-box; }
  html, body { width: 1200px; height: 855px; overflow: hidden; background: var(--backdrop); }
  .spread { position: relative; width: 1200px; height: 855px; }
  .page {
    position: absolute; width: 533px; height: 376px;
    background: var(--paper); overflow: hidden;
    font-family: "Open Sans", sans-serif; color: var(--ink);
  }
  .page--back     { left: 66px;  top: 13px; }
  .page--front    { left: 598px; top: 13px; }
  .page--inside-1 { left: 67px;  top: 438px; }
  .page--inside-2 { left: 600px; top: 438px; border-left: 1px solid var(--rule); }

  /* Studio name set in type, with a plain dot beside it */
  .studio-name {
    position: absolute; display: flex; align-items: center; gap: 8px;
    font-family: "Jost", sans-serif; font-weight: 400; color: var(--ink);
    text-transform: uppercase; letter-spacing: 0.12em; white-space: nowrap;
  }
  .studio-name__dot { display: block; border-radius: 50%; background: var(--ink); flex: none; }
  .page--back .studio-name { left: 0; right: 0; top: 132px; justify-content: center; font-size: 14px; }
  .page--back .studio-name__dot { width: 10px; height: 10px; }
  .page--front .studio-name { left: 18px; top: 308px; font-size: 10px; gap: 6px; }
  .page--front .studio-name__dot { width: 8px; height: 8px; }

  /* Back page */
  .about__title {
    position: absolute; left: 0; right: 0; top: 226px; text-align: center;
    font-family: "Jost", sans-serif; font-weight: 400; font-size: 11.5px; color: var(--ink);
  }
  .about__text {
    position: absolute; left: 164px; top: 244px; width: 204px;
    font-size: 5.2px; line-height: 1.45; color: var(--ink);
  }
  .about__text p + p { margin-top: 5px; }
  .about__web {
    position: absolute; left: 0; right: 0; top: 351px; text-align: center;
    font-family: "Jost", sans-serif; font-size: 8px; letter-spacing: 0.2em; color: var(--ink);
  }

  /* Front page */
  .cover-photo { position: absolute; left: 0; top: 0; width: 533px; height: 227px;
    background: linear-gradient(100deg, var(--photo-mid), var(--photo-dark) 45%, var(--photo-light)); }
  .cover-title { position: absolute; left: 137px; top: 262px;
    font-family: "Oswald", sans-serif; font-weight: 600; color: var(--ink); line-height: 1; }
  .cover-title__year { display: block; font-size: 38px; }
  .cover-title__name { display: block; margin-top: 8px; font-size: 28px; letter-spacing: 0.01em; }

  /* Inside page 1 */
  .includes__title { position: absolute; left: 24px; top: 27px;
    font-family: "Jost", sans-serif; font-weight: 300; font-size: 24px; color: var(--ink-soft); }
  .includes__list { position: absolute; left: 24px; top: 64px; width: 500px;
    font-size: 7.2px; line-height: 14.5px; color: var(--ink-muted); }
  .collection { position: absolute; width: 232px; }
  .collection--1 { left: 24px;  top: 137px; }
  .collection--3 { left: 270px; top: 137px; }
  .collection--2 { left: 24px;  top: 238px; }
  .collection--4 { left: 270px; top: 238px; }
  .collection__name { font-family: "Jost", sans-serif; font-weight: 300; font-size: 24px;
    color: var(--ink-soft); line-height: 1.1; }
  .collection__text { margin-top: 6px; font-size: 6.8px; line-height: 1.45; color: var(--ink-muted); text-align: justify; }
  .collection__text + .collection__text { margin-top: 8px; }

  /* Inside page 2 */
  .rule-bar { position: absolute; top: 0; height: 6px; background: var(--rule); }
  .rule-bar--left { left: 27px; width: 188px; }
  .rule-bar--right { left: 264px; width: 269px; }
  .item { position: absolute; width: 196px; }
  .item--right { left: 264px; width: 252px; }
  .item--left { left: 27px; }
  .item__name { font-family: "Jost", sans-serif; font-weight: 300; font-size: 11px;
    line-height: 1.3; color: var(--ink-soft); text-transform: uppercase; }
  .item__name span { margin-left: 14px; }
  .item__text { margin-top: 3px; font-family: "Pathway Gothic One", sans-serif;
    font-size: 7.6px; line-height: 1.3; color: var(--ink-muted); }
  .detail-photo { position: absolute; }
  .detail-photo--child { left: 23px; top: 239px; width: 188px; height: 137px;
    background: linear-gradient(135deg, var(--photo-light), var(--photo-mid)); }
  .detail-photo--family { left: 264px; top: 280px; width: 125px; height: 96px;
    background: linear-gradient(135deg, var(--photo-light), var(--photo-mid)); }
  .detail-photo--siblings { left: 389px; top: 280px; width: 144px; height: 96px;
    background: linear-gradient(135deg, var(--photo-mid), var(--photo-dark)); }
</style>
</head>
<body>
<main class="spread">

  <section class="page page--back">
    <div class="studio-name"><span class="studio-name__dot"></span><span>Marrowfield</span></div>
    <h2 class="about__title">About us</h2>
    <div class="about__text">
      <p>Marrowfield Studio, based in Frankfurt, Germany, is a newly launched studio led by American photographer Clara Wrenholt. She specializes in portrait, children and cause-related photography, and is currently working on a collection featuring mothers and children.</p>
      <p>Clara holds a Master's in Foreign Service and International Development from Ashgrove University, and a BA from Linwood College. She is available for assignments worldwide.</p>
    </div>
    <p class="about__web">www.marrowfieldstudio.com</p>
  </section>

  <section class="page page--front">
    <div class="cover-photo" role="img" aria-label="Black and white portrait of three smiling children lying together"></div>
    <div class="studio-name"><span class="studio-name__dot"></span><span>Marrowfield</span></div>
    <h1 class="cover-title">
      <span class="cover-title__year">2013</span>
      <span class="cover-title__name">PHOTOGRAPHY COLLECTIONS</span>
    </h1>
  </section>

  <section class="page page--inside-1">
    <h2 class="includes__title">All collections&nbsp; include:</h2>
    <div class="includes__list">
      <p>One to two hour portrait session with photographer in location of your choice</p>
      <p>(unlimited time if necessary!)</p>
      <p>Clara will create a presentation video with hand-selected music and custom editing, which tells your story, highlights the best images, and reveals the connections within your family. An online gallery for viewing and ordering helps you share your images with family and friends.</p>
    </div>

    <article class="collection collection--1">
      <h3 class="collection__name">Collection 1: 300 €</h3>
      <p class="collection__text">Your favorite five images from the session will be professionally edited and presented to you on disk as high resolution jpegs</p>
    </article>
    <article class="collection collection--3">
      <h3 class="collection__name">Collection 3: 500 €</h3>
      <p class="collection__text">Your favorite fifteen images from the session will be professionally edited and presented to you on disk as high resolution jpegs Your favorite two images from the session will be professionally printed for you (20x30cm) on Larchmere paper, Clara's favorite for portraits.</p>
    </article>
    <article class="collection collection--2">
      <h3 class="collection__name">Collection 2: 400 €</h3>
      <p class="collection__text">Your favorite ten images from the session will be professionally edited and given to you on disk as high resolution jpegs Your favorite image from the session will be professionally printed for you (20x30cm) on Larchmere paper, Clara's favorite for portraits.</p>
    </article>
    <article class="collection collection--4">
      <h3 class="collection__name">Collection 4: 600 €</h3>
      <p class="collection__text">ALL presented images from the session will be professionally edited and presented to you on disk as high resolution jpegs (approximately 40+ images)</p>
      <p class="collection__text">Your favorite two images from the session will be professionally printed for you (20x30cm) on Larchmere paper, Clara's favorite for portraits.</p>
    </article>
  </section>

  <section class="page page--inside-2">
    <div class="rule-bar rule-bar--left"></div>
    <div class="rule-bar rule-bar--right"></div>

    <article class="item item--left" style="top:32px">
      <h3 class="item__name">A la carte</h3>
      <p class="item__text">These products may be purchased separately to complement your collection. A consultation with Clara will help you decide which products are best for gifts and for your home.</p>
    </article>
    <article class="item item--left" style="top:101px">
      <h3 class="item__name">A la carte - 25 € each<br>High resolution digital images</h3>
      <p class="item__text" style="margin-top:9px">Perfect if you just need to add "one more image" to your collection! High-resolution jpeg file</p>
    </article>
    <article class="item item--left" style="top:176px">
      <h3 class="item__name">A la carte - 25 € <span style="margin-left:2px">Matt prints</span></h3>
      <p class="item__text">Each print is professionally edited, printed on archival photo paper. Purchase includes the JPEG file for your personal digital use. 20x30 cm and smaller</p>
    </article>
    <div class="detail-photo detail-photo--child" role="img" aria-label="Black and white close-up portrait of a toddler"></div>

    <article class="item item--right" style="top:32px">
      <h3 class="item__name">A la carte - 45 €<span>Larchmere prints</span></h3>
      <p class="item__text">Prints on Larchmere (watercolor) paper are Clara's favorite for large format color prints 30x40 cm</p>
    </article>
    <article class="item item--right" style="top:81px">
      <h3 class="item__name">A la carte - 100 €<span>Canvas prints</span></h3>
      <p class="item__text">Ready-to-hang, stretched canvas wall art of your favorite images 30x40 cm</p>
    </article>
    <article class="item item--right" style="top:134px">
      <h3 class="item__name">A la carte - 350 €<span>Framed + matted prints</span></h3>
      <p class="item__text">Beautiful Larchmere prints finished with wide mats and simple, elegant frames of your choice 30x40 inch</p>
    </article>
    <article class="item item--right" style="top:185px">
      <h3 class="item__name">Prices begin at - 100 €<br>Custom designed albums</h3>
      <p class="item__text">Images from your session are selected for the custom design of an album and bound in a book for a modern presentation of your images. There are a number of cover choices for the classic flush-mount and beautifully crafted albums. A great way to display all of your favorite images from your session on your coffee table.</p>
    </article>
    <div class="detail-photo detail-photo--family" role="img" aria-label="Black and white photo of a mother with two children on a bed"></div>
    <div class="detail-photo detail-photo--siblings" role="img" aria-label="Black and white photo of two laughing children"></div>
  </section>

</main>
</body>
</html>
```